Business Card Design Project - del varosi group

dear Sirs

we need business card design for our group ( DEL Varosi Group ) , i have got the Logo design of our group from pixel harbor in previous , so all need details relating to our group i think available with you, as well as the the chosen logo design

we hope to provide us with business card logo that to be appropaite and satisfactory to us .

thanks

note : logo design of our group is attached .
Updates

Reason: please extend the deadline of my project for additional 15 days because i didn't received appropriate design for our gruop yet . kindly beaware that i have received 77 design till now , supossed to send me 200-250 design at least . thanks

Target Market(s)

contents

name : Kerem EL Nadiri

position : Operation Manager

Industry/Entity Type

Business

Requirements
Must have

• person name

group logo
Nice to have
• logo color matching with back background

```html
<!DOCTYPE html>
<html lang="en">
<head>
<meta charset="utf-8">
<title>DEL Varosi Group – Business Card</title>
<link href="https://fonts.googleapis.com/css2?family=Libre+Baskerville:wght@700&family=Tinos:wght@400;700&display=swap" rel="stylesheet">
<style>
  :root {
    --page: #e6e8eb;
    --card-white: #ffffff;
    --brand-blue: #0e4a8a;
    --brand-blue-soft: #5f86b8;
    --stripe-dark: #2b2e33;
    --ink-blue: #0d3f7c;
    --ink-grey: #8a8d91;
    --ink-white: #ffffff;
  }
  html, body {
    margin: 0;
    padding: 0;
    width: 1067px;
    height: 1200px;
    overflow: hidden;
    background: var(--page);
  }
  .canvas {
    position: relative;
    width: 1067px;
    height: 1200px;
  }
  .card {
    position: absolute;
    left: 233px;
    width: 600px;
    height: 343px;
    box-shadow: 0 10px 28px rgba(0,0,0,0.22);
    overflow: hidden;
  }
  .card--front { top: 110px; background: var(--card-white); }
  .card--back  { top: 700px; background: var(--brand-blue); }
  .card__shape {
    position: absolute;
    inset: 0;
    width: 100%;
    height: 100%;
  }
  .holder {
    position: absolute;
    top: 22px;
    right: 30px;
    text-align: right;
  }
  .holder__name {
    margin: 0;
    font-family: "Libre Baskerville", Georgia, serif;
    font-weight: 700;
    font-size: 27px;
    color: var(--ink-blue);
    letter-spacing: 0.2px;
  }
  .holder__title {
    margin: 4px 0 0;
    font-family: "Tinos", "Times New Roman", serif;
    font-size: 16px;
    color: var(--ink-grey);
  }
  .brand {
    position: absolute;
    display: flex;
    align-items: center;
    gap: 10px;
    font-family: "Tinos", "Times New Roman", serif;
    font-weight: 700;
  }
  .brand__mark {
    border: 3px solid currentColor;
    box-sizing: border-box;
  }
  .card--front .brand {
    left: 14px;
    top: 128px;
    color: var(--ink-blue);
    font-size: 25px;
  }
  .card--front .brand__mark { width: 26px; height: 26px; }
  .contact {
    position: absolute;
    right: 24px;
    bottom: 20px;
    margin: 0;
    padding: 0;
    list-style: none;
    text-align: right;
    font-family: "Tinos", "Times New Roman", serif;
    font-size: 15.5px;
    line-height: 19px;
    color: var(--ink-white);
  }
  .card--back .brand {
    left: 50%;
    top: 50%;
    transform: translate(-50%, -50%);
    color: var(--brand-blue-soft);
    font-size: 44px;
    white-space: nowrap;
  }
  .card--back .brand__mark { width: 44px; height: 44px; border-width: 4px; }
</style>
</head>
<body>
<main class="canvas">
  <section class="card card--front" aria-label="Business card front">
    <svg class="card__shape" viewBox="0 0 600 343" preserveAspectRatio="none" aria-hidden="true">
      <polygon points="0,155 225,245 600,120 600,343 0,343" fill="var(--stripe-dark)"/>
      <polygon points="0,163 225,255 600,130 600,343 0,343" fill="var(--brand-blue)"/>
    </svg>
    <div class="holder">
      <h1 class="holder__name">Kerem EL Nadiri</h1>
      <p class="holder__title">Operation Manager</p>
    </div>
    <div class="brand">
      <span class="brand__mark"></span>
      <span class="brand__name">DEL VAROSI GROUP</span>
    </div>
    <ul class="contact">
      <li>Phone: 0123 456 789</li>
      <li>Fax: 0123 456 789</li>
      <li>info@yourdomain.com</li>
      <li>www.yourdomain.com</li>
      <li>PO. Box: City name, etc.</li>
    </ul>
  </section>

  <section class="card card--back" aria-label="Business card back">
    <div class="brand">
      <span class="brand__mark"></span>
      <span class="brand__name">DEL VAROSI GROUP</span>
    </div>
  </section>
</main>
</body>
</html>
```